Business card for event manager / organizer "waiter service"

Draft of a new valuable business card for my company.
Events, personnel service providers, festivals

```html
<!DOCTYPE html>
<html lang="de">
<head>
<meta charset="utf-8">
<title>Jonas Servierteam – Visitenkarte</title>
<link href="https://fonts.googleapis.com/css2?family=Poppins:wght@400;500;700&display=swap" rel="stylesheet">
<style>
  :root {
    --stage: #2b2b2b;
    --card-black: #151515;
    --ink: #111111;
    --white: #ffffff;
    --orange: #f07f1a;
    --brown: #8a3f12;
    --grey: #444444;
    --photo-a: #6a6a6a;
    --photo-b: #2a2a2a;
  }
  * { box-sizing: border-box; margin: 0; padding: 0; }
  html, body { width: 1200px; height: 689px; overflow: hidden; }
  body {
    background: var(--stage);
    font-family: "Poppins", sans-serif;
    position: relative;
  }
  .card {
    position: absolute;
    top: 182px;
    width: 520px;
    height: 325px;
    border-radius: 18px;
    overflow: hidden;
  }
  /* back side */
  .card--back {
    left: 60px;
    background: linear-gradient(135deg, #262626, var(--card-black) 60%, #0c0c0c);
  }
  .back-name {
    position: absolute;
    left: 0; right: 0; top: 145px;
    text-align: center;
    color: var(--white);
    font-weight: 700;
    font-size: 26px;
    letter-spacing: 0.5px;
  }
  /* front side */
  .card--front {
    left: 620px;
    background: var(--white);
  }
  .brand {
    position: absolute;
    left: 28px; top: 40px;
  }
  .brand-row { display: flex; align-items: center; gap: 10px; }
  .brand-mark {
    width: 26px; height: 26px;
    background: var(--orange);
    border-radius: 4px;
  }
  .brand-name {
    font-weight: 700;
    font-size: 27px;
    color: var(--ink);
    line-height: 1;
  }
  .brand-tagline {
    margin: 6px 0 0 36px;
    font-size: 9.5px;
    color: var(--grey);
  }
  .photo {
    position: absolute;
    right: 34px; top: 22px;
    width: 112px; height: 112px;
    border-radius: 50%;
    background: radial-gradient(circle at 50% 40%, var(--photo-a), var(--photo-b));
  }
  .person {
    position: absolute;
    right: 30px; top: 146px;
    text-align: right;
  }
  .person-name { color: var(--orange); font-weight: 500; font-size: 15px; letter-spacing: 0.3px; }
  .person-role { color: var(--ink); font-size: 12px; }
  .contacts {
    position: absolute;
    left: 28px; top: 140px;
    list-style: none;
  }
  .contact {
    display: flex; align-items: center; gap: 8px;
    font-size: 12.5px; color: var(--ink);
    height: 21px;
  }
  .contact-icon { width: 16px; height: 16px; flex: none; }
  .service-band {
    position: absolute;
    left: 0; right: 0; bottom: 0;
    height: 46px;
    display: flex;
  }
  .service-band-text {
    flex: 1;
    background: var(--orange);
    color: var(--white);
    font-size: 14px;
    font-weight: 500;
    display: flex; align-items: center;
    padding-left: 28px;
    letter-spacing: 0.3px;
  }
  .service-band-end { width: 70px; background: var(--card-black); }
</style>
</head>
<body>

<section class="card card--back" aria-label="Kartenrückseite">
  <p class="back-name">Jonas Servierteam</p>
</section>

<section class="card card--front" aria-label="Kartenvorderseite">
  <div class="brand">
    <div class="brand-row">
      <span class="brand-mark"></span>
      <span class="brand-name">Jonas Servierteam</span>
    </div>
    <p class="brand-tagline">...denn die nächste Feier kommt bestimmt!</p>
  </div>

  <div class="photo" role="img" aria-label="Porträtfoto des Inhabers"></div>
  <div class="person">
    <p class="person-name">JONAS BRANDTNER</p>
    <p class="person-role">Inhaber</p>
  </div>

  <ul class="contacts">
    <li class="contact">
      <svg class="contact-icon" viewBox="0 0 16 16"><polygon points="8,0 15,4 15,12 8,16 1,12 1,4" fill="var(--brown)"/><path d="M5.2 4.5l1.6-.4.8 2-1 .7a5 5 0 0 0 2.6 2.6l.7-1 2 .8-.4 1.6c-3.6.2-6.5-2.7-6.3-6.3z" fill="#fff"/></svg>
      0231 555 48 17 | 0170 555 23 90
    </li>
    <li class="contact">
      <svg class="contact-icon" viewBox="0 0 16 16"><polygon points="8,0 15,4 15,12 8,16 1,12 1,4" fill="var(--brown)"/><circle cx="8" cy="8" r="3.8" fill="none" stroke="#fff" stroke-width="1"/><ellipse cx="8" cy="8" rx="1.6" ry="3.8" fill="none" stroke="#fff" stroke-width="0.8"/><line x1="4.2" y1="8" x2="11.8" y2="8" stroke="#fff" stroke-width="0.8"/></svg>
      www.jonas-servierteam.de
    </li>
    <li class="contact">
      <svg class="contact-icon" viewBox="0 0 16 16"><polygon points="8,0 15,4 15,12 8,16 1,12 1,4" fill="var(--brown)"/><rect x="4.3" y="5.5" width="7.4" height="5" fill="none" stroke="#fff" stroke-width="1"/><path d="M4.3 5.5L8 8.5l3.7-3" fill="none" stroke="#fff" stroke-width="1"/></svg>
      info@jonas-servierteam.de
    </li>
    <li class="contact">
      <svg class="contact-icon" viewBox="0 0 16 16"><polygon points="8,0 15,4 15,12 8,16 1,12 1,4" fill="var(--brown)"/><path d="M8 12.2s-3-3.3-3-5.2a3 3 0 0 1 6 0c0 1.9-3 5.2-3 5.2z" fill="#fff"/><circle cx="8" cy="7" r="1.1" fill="var(--brown)"/></svg>
      Lindenweg 12, 44137 Dortmund
    </li>
    <li class="contact">
      <svg class="contact-icon" viewBox="0 0 16 16"><polygon points="8,0 15,4 15,12 8,16 1,12 1,4" fill="var(--brown)"/><circle cx="8" cy="8" r="2.6" fill="#fff"/></svg>
      @jonasservierteam
    </li>
  </ul>

  <div class="service-band">
    <p class="service-band-text">Events | Personnel | Service Providers | Festivals</p>
    <span class="service-band-end"></span>
  </div>
</section>

</body>
</html>
```